BUSINESS CARD DESIGN

NAME- DALE VORSKIN
PHONE NUMER - 555- 714-9082
EMAIL- OFFICE@TRV-GROUNDMAKRZ.COM
BACK OF CARD- SPEACIALIZES IN LAND CLEARING, FORESTRY MUCLHING AND EXCAVATION

Contact Information for Business Card

NAME- DALE VORSKIN PHONE NUMER - 555- 714-9082 EMAIL- OFFICE@TRV-GROUNDMAKRZ.COM BACK OF CARD- SPEACIALIZES IN LAND CLEARING , MUCLHING AND EXCAVATION

```html
<!DOCTYPE html>
<html lang="en">
<head>
<meta charset="utf-8">
<title>Traverse Ground Makrz – Business Card</title>
<link rel="stylesheet" href="https://fonts.googleapis.com/css2?family=Audiowide&display=swap">
<style>
  :root {
    --page: #ffffff;
    --card: #000000;
    --green: #22ff12;
    --silver: #c9c9c9;
    --light: #e6e6e6;
  }
  * { margin: 0; padding: 0; box-sizing: border-box; }
  html, body { width: 1200px; height: 1131px; overflow: hidden; background: var(--page); }
  body { position: relative; font-family: "Audiowide", sans-serif; }

  .card {
    position: absolute;
    left: 256px;
    width: 689px;
    height: 394px;
    background: var(--card);
    overflow: hidden;
  }
  .card--front { top: 106px; }
  .card--back { top: 592px; }
  .card__band {
    position: absolute;
    left: 0; right: 0;
    top: 376px;
    height: 9px;
    background: var(--green);
  }

  .brand {
    position: absolute;
    display: flex;
    align-items: center;
    gap: 10px;
    color: var(--green);
    text-transform: uppercase;
    line-height: 1.15;
  }
  .brand__dot {
    flex: none;
    border-radius: 50%;
    background: var(--green);
  }
  .card--front .brand { left: 70px; top: 150px; font-size: 17px; }
  .card--front .brand__dot { width: 30px; height: 30px; }
  .card--back .brand {
    left: 0; right: 0; top: 180px;
    justify-content: center;
    font-size: 21px;
  }
  .card--back .brand__dot { width: 36px; height: 36px; }

  .identity {
    position: absolute;
    left: 343px;
    top: 84px;
    height: 74px;
    border-left: 4px solid var(--green);
    padding-left: 15px;
    color: var(--silver);
    font-size: 22px;
    letter-spacing: 1.5px;
    line-height: 36px;
  }
  .identity__name { margin-top: 0; }

  .contacts {
    position: absolute;
    left: 352px;
    top: 232px;
    list-style: none;
  }
  .contacts__item {
    display: flex;
    align-items: center;
    height: 20px;
    margin-bottom: 16px;
    color: var(--light);
    font-size: 11px;
    letter-spacing: 1px;
  }
  .contacts__item:nth-child(2) { margin-bottom: 12px; }
  .contacts__icon {
    width: 20px; height: 20px;
    margin-right: 16px;
    fill: none;
    stroke: var(--green);
    stroke-width: 1.4;
  }

  .tagline {
    position: absolute;
    left: 0; right: 0;
    top: 296px;
    text-align: center;
    color: var(--green);
    font-size: 11px;
    line-height: 13px;
    letter-spacing: 0.5px;
  }
</style>
</head>
<body>

  <section class="card card--front">
    <div class="brand">
      <span class="brand__dot"></span>
      <span class="brand__name">Traverse Ground<br>Makrz LLC</span>
    </div>

    <div class="identity">
      <p class="identity__name">DALE VORSKIN</p>
      <p class="identity__role">OWNER</p>
    </div>

    <ul class="contacts">
      <li class="contacts__item">
        <svg class="contacts__icon" viewBox="0 0 20 20" aria-hidden="true">
          <path d="M5 2.5l3 3.5-1.6 2a9 9 0 0 0 5.6 5.6l2-1.6 3.5 3-1.8 2.2C9.5 17 3 10.5 2.8 4.3z"/>
          <path d="M12 3.5a5 5 0 0 1 4.5 4.5M12 6.2a2.5 2.5 0 0 1 1.8 1.8"/>
        </svg>
        +555- 714-9082
      </li>
      <li class="contacts__item">
        <svg class="contacts__icon" viewBox="0 0 20 20" aria-hidden="true">
          <rect x="1" y="4" width="18" height="12"/>
          <circle cx="6" cy="9" r="1.8"/>
          <path d="M3.5 13.5a2.5 2.5 0 0 1 5 0M11 8h6M11 10.5h6M11 13h4"/>
        </svg>
        OFFICE@TRV-GROUNDMAKRZ.COM
      </li>
      <li class="contacts__item">
        <svg class="contacts__icon" viewBox="0 0 20 20" aria-hidden="true">
          <circle cx="10" cy="10" r="8"/>
          <ellipse cx="10" cy="10" rx="3.5" ry="8"/>
          <path d="M2 10h16M3.2 6h13.6M3.2 14h13.6"/>
        </svg>
        WWW.GROUNDMAKRZ.COM
      </li>
    </ul>

    <div class="card__band"></div>
  </section>

  <section class="card card--back">
    <div class="brand">
      <span class="brand__dot"></span>
      <span class="brand__name">Traverse Ground<br>Makrz LLC</span>
    </div>

    <p class="tagline">SPEACIALIZES IN LAND CLEARING<br>MUCLHING AND EXCAVATION</p>

    <div class="card__band"></div>
  </section>

</body>
</html>
```